Meridale Accountants needs a stationery design

We need a stationery design for our new innovative accountancy practise - it is to look professional and reliable but also minimalist, crisp, innovative and fresh. Avoid the use of block colour. You must include letterhead.

We look after business clients and help them get started and grow to successful companies. We provide a range of software, accounting, taxation and business consulting services to these clients.

This is a spin off from our more traditional existing practise - we would like to use the same green and blue.

The final design should communicate professional expertise coupled with innovative technology and personal care. The font of the type should reflect this - so far we have received standard font only.

We need business cards, letterhead, with comp slips, We need to see the whole set to form a view, not just the businesscard

I have uploaded the colours that we want to use from our existing letterhead, being the green and blue. We need to use the KTR logo - also enclosed - please use the text from the enclosed letterhead, but don't refer to this for design purposes - this was our temporary draft only.

Target Market(s)

Small to medium companies, high wealth investor clients

Industry/Entity Type

Professional Service

Requirements
Must have
• Crisp, simple design but evoking innovation, technology, competence and difference.
• So far the designs are too standard and not showing innovation.

```html
<!DOCTYPE html>
<html lang="en">
<head>
<meta charset="utf-8">
<title>Meridale Accountants – Stationery Set</title>
<link href="https://fonts.googleapis.com/css2?family=Oswald:wght@300&family=Roboto+Condensed:wght@400;700&family=Roboto:wght@400;700&display=swap" rel="stylesheet">
<style>
:root{
  --bg:#d1e09d;
  --green:#7d9b33;
  --green-dark:#66842a;
  --green-light:#b5cf62;
  --blue:#1f4f9e;
  --navy:#1d2f5c;
  --paper:#ffffff;
  --ink:#2a3550;
  --shadow:0 3px 8px rgba(60,80,20,.25);
}
*{box-sizing:border-box;margin:0;padding:0}
html,body{width:1200px;height:900px;overflow:hidden}
body{background:var(--bg);position:relative;font-family:"Roboto Condensed",sans-serif;color:var(--ink)}
.sheet{position:absolute;background:linear-gradient(180deg,#fff 55%,#f3f7ea 100%);box-shadow:var(--shadow);overflow:hidden}
.wordmark{font-family:"Oswald",sans-serif;font-weight:300;color:var(--green);text-align:center;line-height:1;letter-spacing:.22em}
.wordmark .name{display:block}
.wordmark .sub{display:block;letter-spacing:.3em}
.motto{display:block;font-family:"Roboto Condensed",sans-serif;color:var(--navy);text-align:center;letter-spacing:.08em;line-height:1.2}
.footer-bar{position:absolute;left:0;right:0;bottom:0;height:4px;background:linear-gradient(90deg,var(--green) 0 78%,var(--paper) 78% 79%,var(--blue) 79%)}
.contact-line{position:absolute;font-size:4.6px;color:var(--navy);white-space:nowrap;line-height:1.6}
.member{position:absolute;display:flex;align-items:center;gap:3px;font-size:3.6px;color:var(--navy);line-height:1.2;text-align:right}
.member .badge{width:12px;height:12px;background:var(--blue)}

/* small card stacks */
.card-stack{position:absolute;width:84px;height:36px;background:#fff;box-shadow:0 2px 0 #e4e8dc,0 4px 0 #d6dccb,var(--shadow)}
.card-stack .wordmark{margin-top:5px}
.card-stack .name{font-size:10px}
.card-stack .sub{font-size:4px;margin-top:2px}
.card-stack .motto{font-size:3.6px;margin-top:2px}

/* envelope front */
.envelope{left:96px;top:150px;width:328px;height:164px}
.envelope .wordmark{position:absolute;left:22px;top:22px;width:82px}
.envelope .name,.slip .name{font-size:15px}
.envelope .sub,.slip .sub{font-size:5.4px;margin-top:3px}
.envelope .motto,.slip .motto,.letterhead .motto,.envelope-back .motto{font-size:4.6px;margin-top:2px}

/* envelope back */
.envelope-back{left:90px;top:348px;width:330px;height:210px;background:#fff}
.envelope-back .flap{position:absolute;left:0;top:0}
.envelope-back .wordmark{position:absolute;left:125px;top:128px;width:82px}
.envelope-back .name{font-size:15px}
.envelope-back .sub{font-size:5.4px;margin-top:3px}

/* compliments slip */
.slip{left:85px;top:598px;width:325px;height:160px}
.slip .wordmark{position:absolute;left:18px;top:20px;width:82px}
.slip .tag{position:absolute;right:16px;top:18px;font-size:8px;color:var(--navy)}

/* letterhead */
.letterhead{left:452px;top:88px;width:330px;height:467px}
.letterhead .wordmark{position:absolute;left:16px;top:20px;width:84px}
.letterhead .name{font-size:15px}
.letterhead .sub{font-size:5.4px;margin-top:3px}
.letterhead .legal{position:absolute;left:30px;top:320px;transform:rotate(-44deg);transform-origin:left top;font-size:9.5px;color:rgba(125,155,51,.12);white-space:nowrap}
.info-block{position:absolute;left:4px;font-size:4.4px;color:var(--navy)}
.info-block h3{font-size:6px;color:var(--green);font-weight:700;border-left:1.5px solid var(--green-dark);border-right:1.5px solid var(--green-dark);padding:0 5px;margin-bottom:3px;display:inline-block;background:linear-gradient(90deg,#eef4dc,#fff)}
.info-block ul{list-style:none}
.info-block li{line-height:1.55;position:relative;padding-left:6px}
.info-block li::before{content:"";position:absolute;left:0;top:1.6px;border-left:3px solid var(--navy);border-top:1.7px solid transparent;border-bottom:1.7px solid transparent}

/* presentation folder */
.folder{left:774px;top:174px;width:334px;height:450px;background:linear-gradient(135deg,#8fae3e 0%,#86a33a 50%,#6f8c2c 100%)}
.folder .texture{position:absolute;inset:0;background:linear-gradient(200deg,rgba(255,255,255,.22) 0%,rgba(255,255,255,.08) 40%,rgba(255,255,255,0) 75%)}
.folder .wordmark{position:absolute;left:0;right:0;top:188px;color:#fff}
.folder .name{font-size:34px}
.folder .sub{font-size:11px;margin-top:6px}
.folder .tagline{position:absolute;left:0;right:0;top:238px;text-align:center;color:#fff;font-family:"Oswald",sans-serif;font-weight:300;font-size:10px;letter-spacing:.12em}
.folder .legal{position:absolute;left:0;right:0;top:256px;text-align:center;color:#fff;font-size:8px}
.folder .edge{position:absolute;left:0;right:0;bottom:0;height:4px;background:linear-gradient(90deg,var(--green-dark) 0 78%,#e8f0cf 78%)}

/* business cards */
.card-front{left:445px;top:630px;width:280px;height:165px;border-radius:8px;background:linear-gradient(120deg,#7a9830 0%,#9ab84a 45%,#c9de8a 100%)}
.card-front .wordmark{position:absolute;left:0;right:0;top:45px;color:#fff}
.card-front .name{font-size:24px}
.card-front .sub{font-size:8px;margin-top:4px}
.card-front .tagline{position:absolute;left:0;right:0;top:88px;text-align:center;color:#fff;font-family:"Oswald",sans-serif;font-weight:300;font-size:7px;letter-spacing:.14em}
.card-front .details{position:absolute;left:0;right:0;top:110px;text-align:center;color:#fff;font-size:5.6px;line-height:1.8}

.card-back{left:755px;top:640px;width:280px;height:165px;border-radius:8px;background:linear-gradient(180deg,#fff 60%,#f1f5e6)}
.card-back .nameplate{position:absolute;right:0;top:22px;width:125px;padding:3px 8px 3px 24px;background:linear-gradient(90deg,rgba(181,207,98,0) 0%,#cfe08f 30%,#b5cf62 100%);text-align:right}
.card-back .person{font-family:"Roboto",sans-serif;font-weight:700;font-size:11px;color:var(--navy)}
.card-back .role{font-size:7px;color:var(--green-dark)}
.card-back .lines{position:absolute;left:25px;top:76px;font-size:6.2px;color:var(--navy)}
.card-back .lines div{display:flex;align-items:center;gap:6px;margin-bottom:5px}
.card-back .member{right:16px;bottom:14px}
</style>
</head>
<body>

<!-- small card stacks -->
<div class="card-stack" style="left:228px;top:88px">
  <div class="wordmark"><span class="name">MERIDALE</span><span class="sub">ACCOUNTANTS</span></div>
  <span class="motto">Chartered accountants</span>
</div>
<div class="card-stack" style="left:348px;top:92px">
  <div class="wordmark"><span class="name">MERIDALE</span><span class="sub">ACCOUNTANTS</span></div>
  <span class="motto">Chartered accountants</span>
</div>

<!-- DL envelope front -->
<div class="sheet envelope">
  <div class="wordmark"><span class="name">MERIDALE</span><span class="sub">ACCOUNTANTS</span><span class="motto">Achieve with Meridale</span></div>
  <div class="contact-line" style="left:10px;top:138px">A : Suite 4B, Level 1, 27 Linden Road, Ferndale NSW 2600 &nbsp; T : (02) 5550 1420 &nbsp; M : 0400 555 218 &nbsp; P : P O Box 2210, Ferndale NSW 2600<br>&nbsp;&nbsp;&nbsp;&nbsp;&nbsp;&nbsp;&nbsp;E : clients@meridaleaccountants.com.au &nbsp; W : meridaleaccountants.com.au &nbsp;&nbsp;&nbsp;&nbsp; ABN 41 205 318 774</div>
  <div class="member" style="right:10px;top:140px"><span>Meridale Accountants is a<br>KTR Practice</span><span class="badge"></span></div>
  <div class="footer-bar"></div>
</div>

<!-- envelope back -->
<div class="sheet envelope-back">
  <svg class="flap" width="330" height="80" viewBox="0 0 330 80">
    <polygon points="18,40 312,40 300,78 30,78" fill="#7d9b33" opacity=".95"/>
  </svg>
  <div class="wordmark"><span class="name">MERIDALE</span><span class="sub">ACCOUNTANTS</span><span class="motto">Achieve with Meridale</span></div>
</div>

<!-- compliments slip -->
<div class="sheet slip">
  <div class="wordmark"><span class="name">MERIDALE</span><span class="sub">ACCOUNTANTS</span><span class="motto">Achieve with Meridale</span></div>
  <div class="tag">With Compliments</div>
  <div class="contact-line" style="left:8px;top:132px">A : Suite 4B, Level 1, 27 Linden Road, Ferndale NSW 2600 &nbsp; T : (02) 5550 1420 &nbsp; M : 0400 555 218 &nbsp; P : P O Box 2210, Ferndale NSW 2600<br>&nbsp;&nbsp;&nbsp;&nbsp;&nbsp;&nbsp;&nbsp;E : clients@meridaleaccountants.com.au &nbsp; W : meridaleaccountants.com.au &nbsp;&nbsp;&nbsp;&nbsp; ABN 41 205 318 774</div>
  <div class="member" style="right:10px;top:134px"><span>Meridale Accountants is a<br>KTR Practice</span><span class="badge"></span></div>
  <div class="footer-bar"></div>
</div>

<!-- letterhead -->
<div class="sheet letterhead">
  <div class="wordmark"><span class="name">MERIDALE</span><span class="sub">ACCOUNTANTS</span><span class="motto">Achieve with Meridale</span></div>
  <div class="legal">Liability Limited by a Scheme Approved Under Professional Standards Legislation</div>
  <div class="info-block" style="top:385px">
    <h3>Services</h3>
    <ul><li>Taxation</li><li>Business Consulting</li><li>Software</li><li>Accounting</li><li>Bookkeeping</li></ul>
  </div>
  <div class="info-block" style="top:434px">
    <h3>Contact</h3>
  </div>
  <div class="contact-line" style="left:6px;top:446px;font-size:3.9px">T : (02) 5550 1420 | M : 0400 555 218 | A : Suite 4B, Level 1, 27 Linden Road, Ferndale NSW 2600 |<br>P : P O Box 2210, Ferndale NSW 2600 | E : clients@meridaleaccountants.com.au | W : meridaleaccountants.com.au | ABN 41 205 318 774</div>
  <div class="member" style="right:8px;top:446px"><span>Meridale Accountants is a<br>KTR Practice</span><span class="badge"></span></div>
  <div class="footer-bar"></div>
</div>

<!-- presentation folder -->
<div class="sheet folder">
  <div class="texture" role="img" aria-label="Faint repeated tagline texture across the folder"></div>
  <div class="wordmark"><span class="name">MERIDALE</span><span class="sub">ACCOUNTANTS</span></div>
  <div class="tagline">Achieve with Meridale</div>
  <div class="legal">Liability Limited by a Scheme Approved Under Professional Standards Legislation</div>
  <div class="edge"></div>
</div>

<!-- business card front -->
<div class="sheet card-front">
  <div class="wordmark"><span class="name">MERIDALE</span><span class="sub">ACCOUNTANTS</span></div>
  <div class="tagline">Achieve with Meridale</div>
  <div class="details">W : meridaleaccountants.com.au<br>A : Suite 4B, Level 1, 27 Linden Road, Ferndale NSW 2600<br>P : P O Box 2210, Ferndale NSW 2600</div>
</div>

<!-- business card back -->
<div class="sheet card-back">
  <div class="nameplate">
    <div class="person">Mr. Example</div>
    <div class="role">Chartered Accountant</div>
  </div>
  <div class="lines">
    <div><svg width="7" height="7" viewBox="0 0 10 10"><path d="M2 1h2l1 2.5-1.3 1a6 6 0 0 0 2.8 2.8l1-1.3L10 7v2a1 1 0 0 1-1 1A9 9 0 0 1 0 1a1 1 0 0 1 1-1z" fill="#1d2f5c"/></svg>(02) 5550 1420</div>
    <div><svg width="7" height="7" viewBox="0 0 10 10"><rect x="2.5" y="0" width="5" height="10" rx="1" fill="#1d2f5c"/><rect x="3.5" y="1.2" width="3" height="6" fill="#fff"/></svg>0400 555 218</div>
    <div><svg width="7" height="7" viewBox="0 0 10 10"><rect x="0" y="2" width="10" height="6.5" fill="#1d2f5c"/><path d="M0 2l5 3.5L10 2" stroke="#fff" stroke-width=".8" fill="none"/></svg>clients@meridaleaccountants.com.au</div>
  </div>
  <div class="member"><span>Meridale Accountants is a<br>KTR Practice</span><span class="badge"></span></div>
</div>

</body>
</html>
```